Business card design for a dynamic IT consulting company

We need a business card design for a young firm, specialized in the Telecommunications/Consulting industry. The name of the company is Quindor and Partners Business Consulting Ltd. (Short name: Quindor and Partnes)
Quindor = solve read reverse, so we aim to be uncomplicated and solution-oriented. The small pipe in our logo is also related to the word solve. So we need a new business card design, which is simple, eye catching and something non traditional (I would probably prefer a square shaped design rather than a rectangle, but open for suggestions). Attached our logo.

Target Market(s)

Usually our customers are Tier1 Telecoms providers (Q-Netra, Palorix, etc) and their executives.

Industry/Entity Type

Business

Contact Information for Business Card

Name: Bence Tolnavari
Email: b.tolnavari@quindor.hu
Web: www.quindor.hu
Mobile: +36 30 518 2769
Title: Managing Director

Optional:
Company name: Quindor and Partners Ltd.
Address: 1087 Budapest, Tolvenka str. 28/C, Hungary

Font styles to use
Other font styles liked:
• helveticaneue_medium, Prime Regular are used now.

Colors

Designer to choose colors to be used in the design.

Requirements
Must have
• I would like to have a 2 sided design.
Nice to have
• I thought if we make the logo a bit bigger (without the company name), that could go to the back with the company name below. I though, if the pipe in the logo is somehow touchable on the business card, would be nice and unique.

```html
<!DOCTYPE html>
<html lang="en">
<head>
<meta charset="utf-8">
<title>Quindor &amp; Partners – Business Card</title>
<link rel="stylesheet" href="https://fonts.googleapis.com/css2?family=Arimo:wght@400;700&display=swap">
<style>
  :root {
    --backdrop: #e4e4e3;
    --paper: #f7f7f6;
    --slate: #5b5c5e;
    --ink: #58595b;
    --brand-blue: #0a93d5;
    --brand-magenta: #a8288f;
    --white: #ffffff;
  }
  * { margin: 0; padding: 0; box-sizing: border-box; }
  html, body {
    width: 1200px;
    height: 960px;
    overflow: hidden;
    background: var(--backdrop);
    font-family: "Arimo", Helvetica, Arial, sans-serif;
  }
  .canvas { position: relative; width: 1200px; height: 960px; }

  .card {
    position: absolute;
    top: 309px;
    width: 342px;
    height: 343px;
  }
  .card--front { left: 235px; background: var(--paper); }
  .card--back { left: 623px; background: var(--slate); }

  /* Front */
  .wordmark {
    position: absolute;
    left: 38px;
    top: 46px;
    display: flex;
    align-items: center;
    gap: 9px;
  }
  .wordmark__square {
    width: 12px;
    height: 12px;
    background: var(--brand-magenta);
  }
  .wordmark__name {
    font-size: 27px;
    font-weight: 400;
    color: var(--ink);
    letter-spacing: -0.2px;
    line-height: 1;
  }

  .person {
    position: absolute;
    left: 38px;
    top: 140px;
  }
  .person__name {
    font-size: 20px;
    font-weight: 700;
    color: var(--brand-blue);
    line-height: 24px;
  }
  .person__title {
    font-size: 15px;
    color: var(--ink);
    letter-spacing: 0.4px;
    line-height: 20px;
  }

  .divider {
    position: absolute;
    left: 38px;
    top: 193px;
    display: flex;
    gap: 3px;
  }
  .divider span { display: block; width: 84px; height: 2px; }
  .divider .divider--grey { background: var(--ink); }
  .divider .divider--magenta { background: var(--brand-magenta); }
  .divider .divider--blue { background: var(--brand-blue); width: 86px; }

  .contact {
    position: absolute;
    left: 38px;
    top: 207px;
    font-size: 13.5px;
    line-height: 18.5px;
    color: var(--ink);
    font-style: normal;
  }
  .contact__block + .contact__block { margin-top: 10px; }

  /* Back */
  .back-mark {
    position: absolute;
    left: 0;
    right: 0;
    top: 150px;
    display: flex;
    justify-content: center;
    align-items: center;
    gap: 10px;
  }
  .back-mark__square {
    width: 14px;
    height: 14px;
    background: var(--brand-blue);
  }
  .back-mark__name {
    font-size: 26px;
    color: var(--white);
    line-height: 1;
  }
  .web {
    position: absolute;
    left: 0;
    right: 0;
    top: 293px;
    text-align: center;
    font-size: 13px;
    letter-spacing: 8px;
    color: var(--white);
    padding-left: 8px;
  }
</style>
</head>
<body>
<main class="canvas">
  <section class="card card--front" aria-label="Business card front">
    <div class="wordmark">
      <span class="wordmark__square"></span>
      <span class="wordmark__name">Quindor &amp; Partners</span>
    </div>

    <div class="person">
      <h1 class="person__name">BENCE TOLNAVARI</h1>
      <p class="person__title">MANAGING DIRECTOR</p>
    </div>

    <div class="divider" aria-hidden="true">
      <span class="divider--grey"></span>
      <span class="divider--magenta"></span>
      <span class="divider--blue"></span>
    </div>

    <address class="contact">
      <p class="contact__block">Quindor and Partners Ltd.<br>1087 Budapest<br>Tolvenka str. 28/C, Hungary</p>
      <p class="contact__block">Mobile: +36 30 518 2769<br>Email: b.tolnavari@quindor.hu</p>
    </address>
  </section>

  <section class="card card--back" aria-label="Business card back">
    <div class="back-mark">
      <span class="back-mark__square"></span>
      <span class="back-mark__name">Quindor &amp; Partners</span>
    </div>
    <p class="web">www.quindor.hu</p>
  </section>
</main>
</body>
</html>
```